Computer Training in the Education sector - Letterhead

We need a new letter head to be designed for the company. We provide computer training fro the Education Sector, both primary and private tertiary providers. The colours will need to tie in with the website www.crossingthestream.co.nz.
The company name is Crossing the Stream with the tag line of Computer Training for Educators.
The footer will need to have the following detail...
0508 PCS MENTOR
021 839 415
www.crossingthestream.co.nz / training@crossingthestream.co.nz
Updates

Thanks for the designs so far.

Some have watermarks in the background. Please don't worry about using watermarks as I will not be using a watermark in in a final design.
Regards,
Roger

Thank you for all the designs and the effort. There was some great concepts that came through.

Cheers
Roger

Industry/Entity Type

Computer

```html
<!DOCTYPE html>
<html lang="en">
<head>
<meta charset="utf-8">
<title>Crossing the Stream – Letterhead</title>
<link rel="stylesheet" href="https://fonts.googleapis.com/css2?family=Open+Sans:wght@400&family=Arimo:wght@400&display=swap">
<style>
  :root {
    --brand-blue: #2f75b9;
    --brand-orange: #e27f35;
    --paper: #ffffff;
    --ink: #262626;
    --ink-soft: #444444;
    --rule: #555555;
  }
  html, body {
    margin: 0;
    padding: 0;
    width: 1034px;
    height: 1200px;
    overflow: hidden;
    background: var(--paper);
  }
  .letterhead {
    position: relative;
    width: 1034px;
    height: 1200px;
    background: var(--paper);
    overflow: hidden;
  }
  .header-swoosh {
    position: absolute;
    top: 0;
    left: 0;
    width: 1034px;
    height: 320px;
  }
  .header-phone {
    position: absolute;
    top: 52px;
    right: 57px;
    margin: 0;
    font-family: "Open Sans", sans-serif;
    font-size: 25px;
    color: var(--paper);
    letter-spacing: 0.2px;
  }
  .brand-name {
    position: absolute;
    top: 82px;
    left: 38px;
    margin: 0;
    font-family: "Open Sans", sans-serif;
    font-weight: 400;
    font-size: 34px;
    line-height: 40px;
    color: var(--brand-blue);
  }
  .tagline {
    position: absolute;
    top: 148px;
    left: 257px;
    margin: 0;
    font-family: "Arimo", sans-serif;
    font-size: 24px;
    letter-spacing: 1.6px;
    color: var(--ink);
  }
  .footer {
    position: absolute;
    left: 182px;
    top: 1134px;
    width: 670px;
  }
  .footer-rule {
    height: 2px;
    background: linear-gradient(to right, rgba(85,85,85,0), var(--rule) 8%, var(--rule) 92%, rgba(85,85,85,0));
  }
  .footer-contacts {
    display: flex;
    justify-content: space-between;
    align-items: center;
    margin-top: 20px;
    font-family: "Open Sans", sans-serif;
    font-size: 14.5px;
    color: var(--ink-soft);
  }
  .footer-divider {
    width: 1px;
    height: 20px;
    background: var(--ink-soft);
  }
</style>
</head>
<body>
  <main class="letterhead">
    <svg class="header-swoosh" viewBox="0 0 1034 320" aria-hidden="true">
      <path fill="var(--brand-orange)" d="M0 0 C 430 16 930 95 1034 312 V0 Z"/>
      <path fill="var(--paper)" d="M0 0 C 420 10 905 70 1034 268 V0 Z"/>
      <path fill="var(--brand-blue)" d="M0 0 C 410 6 895 62 1034 254 V0 Z"/>
    </svg>
    <p class="header-phone">P: 0508 PCS MENTOR</p>

    <h1 class="brand-name">Crossing<br>the Stream</h1>
    <p class="tagline">Computer Training for Educators</p>

    <footer class="footer">
      <div class="footer-rule"></div>
      <div class="footer-contacts">
        <span>P: 021 839 415</span>
        <span class="footer-divider"></span>
        <span>E: training@crossingthestream.co.nz</span>
        <span class="footer-divider"></span>
        <span>W: www.crossingthestream.co.nz</span>
      </div>
    </footer>
  </main>
</body>
</html>
```